Rack Card for Charter Sail Boat business in SF Bay

We are in need of a rack card design to highlight the business to tourists and locals. 2 sided card 3.86" x 8.39" (full bleed)

We are looking for visually appleaing designs on the front and back but a little more detail on the back.

Use the info provided (text and info) on the website to include the 3 key services (Quick, 1/2 day, fullday) and aspects of the boat, location and other key info for customers (not prices). DO NOT INCLUDE ALL THIS TEXT please pick the elements you would like to fit your design and inform the customer as you would like about the business.

I can also provide photos directly from the video if you think those would fit your design. If video doesn't work on this upload you can view it at the website or facebook page (www.fb.com/tidewrenmarinellc)

Target Market(s)

Tourists and locals to san francisco east bay. 25 - 55 years old. Men and women.

Industry/Entity Type

Entertainment

Colors
0455a3
ec1f27
f3f1f8

Requirements
Must have
• Highlight services, key contact information (email, phone, website site), Visual impact
• 2-sided card - 3.86" x 8.39" (98 x 213 mm)
Nice to have
• facebook link, electric engine(green),

```html
<!DOCTYPE html>
<html lang="en">
<head>
<meta charset="utf-8">
<title>Tidewren Marine – Rack Card</title>
<link rel="stylesheet" href="https://fonts.googleapis.com/css2?family=Arimo:wght@400;700&family=Kaushan+Script&family=Oswald:wght@500;600&display=swap">
<style>
:root{
  --page:#ecebf0;
  --blue:#0455a3;
  --blue-deep:#123a82;
  --blue-navy:#0c2a66;
  --red:#ec1f27;
  --red-deep:#b5121b;
  --green:#0f6b2c;
  --yellow:#ffe81a;
  --white:#ffffff;
  --paper:#f3f1f8;
  --sea-light:#cfe3f5;
}
*{box-sizing:border-box;margin:0;padding:0}
html,body{width:1200px;height:1200px;overflow:hidden;background:var(--page)}
.stage{position:relative;width:1200px;height:1200px}
.card{position:absolute;top:116px;width:444px;height:965px;overflow:hidden;
  background:linear-gradient(180deg,#1f55a8 0%,var(--blue-deep) 60%,#0f3274 100%);
  box-shadow:0 6px 18px rgba(0,0,0,.25);font-family:"Arimo",Arial,sans-serif;color:var(--white)}
.card--front{left:108px}
.card--back{left:634px}
.layer{position:absolute;inset:0;width:100%;height:100%}
.abs{position:absolute}
.script{font-family:"Kaushan Script",cursive;font-weight:400}
.condensed{font-family:"Oswald","Arial Narrow",sans-serif;font-weight:500}

/* front */
.hero-photo{position:absolute;left:0;top:0;width:444px;height:300px;
  background:linear-gradient(180deg,#8fb3d6 0%,#f4d9a8 38%,#f1b469 46%,#4a6f98 52%,#27497a 100%)}
.brand{position:absolute;left:232px;top:62px;display:flex;align-items:center;gap:10px}
.brand__dot{width:22px;height:22px;border-radius:50%;background:var(--red)}
.brand__name{font-family:"Kaushan Script",cursive;font-size:30px;color:var(--blue);line-height:1}
.snap{position:absolute;background:var(--white);padding:7px;box-shadow:2px 4px 10px rgba(0,0,0,.45)}
.snap__img{width:100%;height:100%}
.snap--bay{left:215px;top:195px;width:168px;height:150px;transform:rotate(-14deg)}
.snap--bay .snap__img{background:linear-gradient(180deg,#7fb3e6 0%,#b8d6f2 40%,#3c5f7c 50%,#3a7fc2 100%)}
.snap--dock{left:226px;top:312px;width:204px;height:182px;transform:rotate(4deg)}
.snap--dock .snap__img{background:linear-gradient(180deg,#8ec1ee 0%,#c9e0f3 45%,#5a6f85 55%,#2b6ea8 80%,#1d4f84 100%)}
.snap--sail{left:14px;top:470px;width:186px;height:182px;transform:rotate(-4deg)}
.snap--sail .snap__img{background:linear-gradient(160deg,#4f86c6 0%,#9cb9d6 45%,#e6e8ea 60%,#6a7b8a 100%)}
.snap--cabin{left:38px;top:622px;width:176px;height:160px;transform:rotate(15deg)}
.snap--cabin .snap__img{background:linear-gradient(160deg,#c49a72 0%,#e3d1b8 45%,#8d6b52 100%)}

.headline{left:14px;top:270px;width:230px;font-size:26px;line-height:32px}
.headline em{font-style:normal;color:var(--yellow)}
.feature__title{font-size:33px;color:var(--yellow);line-height:1}
.feature__text{font-size:12.4px;line-height:14.2px}
.f-modern{left:242px;top:500px;width:170px}
.f-entertain{left:236px;top:668px;width:190px}
.f-safe{left:20px;top:782px;width:196px}
.feature .feature__text{margin-top:8px}

.booking{position:absolute;left:234px;top:836px;width:192px;height:104px;border:2px solid var(--white);
  border-radius:12px;background:linear-gradient(180deg,#d6232b,var(--red-deep));text-align:center;padding-top:14px}
.booking__lead{font-size:14px;line-height:18px}
.booking__phone{font-size:18px;line-height:24px;font-weight:600}
.booking__mail{font-size:14px;line-height:20px;font-weight:600}

/* back */
.sea-top{position:absolute;left:0;top:0;width:444px;height:240px;
  background:linear-gradient(180deg,#1a3f80 0%,#143a86 45%,#1c4fa0 100%)}
.trip-title{left:16px;top:16px;font-size:40px;line-height:1.1}
.trip-intro{left:16px;top:80px;width:416px;font-size:12.4px;line-height:14.3px}
.map{position:absolute;left:0;top:160px;width:444px;height:640px;
  background:radial-gradient(circle at 40% 45%,#bcd9f2 0%,var(--sea-light) 45%,#e6ede4 80%)}
.tour{position:absolute;border-radius:50%;border:6px solid var(--white);box-shadow:0 3px 10px rgba(0,0,0,.35);
  display:flex;flex-direction:column;align-items:center;justify-content:center;text-align:center;padding:0 22px}
.tour__title{font-size:26px;line-height:1.05;margin-bottom:6px}
.tour__text{font-family:"Oswald","Arial Narrow",sans-serif;font-weight:400;font-size:13.4px;line-height:17px;letter-spacing:-.1px}
.tour--blast{left:231px;top:202px;width:196px;height:196px;background:radial-gradient(circle at 50% 30%,#e02a2e,#b41219);padding-top:6px}
.tour--blast .tour__title{color:var(--yellow)}
.tour--half{left:10px;top:384px;width:200px;height:200px;background:radial-gradient(circle at 50% 30%,#2f45a6,#1a2a86)}
.tour--half .tour__title{color:var(--yellow)}
.tour--full{left:234px;top:586px;width:196px;height:196px;background:radial-gradient(circle at 50% 30%,#17863a,var(--green))}
.tour--full .tour__title{color:var(--yellow)}
.badge{left:14px;top:808px;width:76px;height:76px;border-radius:50%;background:var(--blue-navy);border:3px solid #e9c53a}
.contact-title{left:142px;top:820px;font-size:46px;line-height:1.1}
.contact-row{position:absolute;left:0;width:444px;display:flex;justify-content:center;align-items:center;gap:22px;font-size:16px}
.contact-row--main{top:902px}
.contact-row--web{top:934px;font-size:14px}
.contact-item{display:flex;align-items:center;gap:5px}
.contact-item svg{flex:none}
</style>
</head>
<body>
<main class="stage">

  <!-- Front side -->
  <section class="card card--front">
    <div class="hero-photo" role="img" aria-label="Photo from a sailboat deck looking across the bay at sunset toward the city skyline"></div>
    <svg class="layer" viewBox="0 0 444 965" aria-hidden="true">
      <path d="M0,180 C120,160 230,210 444,300 L444,965 L0,965 Z" fill="#1d52a6"/>
      <path d="M0,232 C110,205 230,235 444,330 L444,300 C260,220 130,178 0,196 Z" fill="#ffffff"/>
      <path d="M0,238 C120,216 240,250 444,345 L444,330 C230,235 110,205 0,232 Z" fill="#ec1f27"/>
      <path d="M0,252 C140,232 250,270 444,365 L444,345 C240,250 120,216 0,238 Z" fill="#b5121b"/>
    </svg>
    <div class="brand"><span class="brand__dot"></span><span class="brand__name">Tidewren Marine</span></div>

    <div class="snap snap--bay"><div class="snap__img" role="img" aria-label="Sunlit bay water with hills and a distant bridge"></div></div>
    <div class="snap snap--dock"><div class="snap__img" role="img" aria-label="The sailboat moored at a marina dock"></div></div>
    <div class="snap snap--sail"><div class="snap__img" role="img" aria-label="Full sail and bow rail out on the bay"></div></div>
    <div class="snap snap--cabin"><div class="snap__img" role="img" aria-label="Bright cabin interior below deck"></div></div>

    <h1 class="abs headline script">Enjoy an amazing experience aboard <em>Tidewren</em> and view San Francisco and the rest of the bay</h1>

    <div class="abs feature f-modern">
      <h2 class="feature__title script">Modern</h2>
      <p class="feature__text">Tidewren is completely electric which means no diesel smells, noise or vibration to suffer. New electrics, plumbing, toilets, and deck areas compliment the elegant lines.</p>
    </div>
    <div class="abs feature f-entertain">
      <h2 class="feature__title script">Entertaining</h2>
      <p class="feature__text">Experience the thrill of sailing Tidewren while we explore Alcatraz and Angel Islands', The Golden Gate and Bay Bridges, the City front or the many other hidden gems.</p>
    </div>
    <div class="abs feature f-safe">
      <h2 class="feature__title script">Safe</h2>
      <p class="feature__text">We carry aboard everything to make your time aboard safe. Life preservers and USCG bulky ones as well as modern self inflating slim comfortable life jackets. Also loaded for every trip is a complete first aid kit, AED, EPIRB, and many other safety items</p>
    </div>

    <div class="booking condensed">
      <p class="booking__lead">For Bookings Contact us Today</p>
      <p class="booking__phone">+1 (415) 555 SAIL (7245)</p>
      <p class="booking__mail">Bookings@TidewrenMarine.com</p>
    </div>
  </section>

  <!-- Back side -->
  <section class="card card--back">
    <div class="sea-top" role="img" aria-label="Dusk view over the bay with the bridge and hills in the distance"></div>
    <div class="map" role="img" aria-label="Map of the bay showing the three cruise routes"></div>
    <svg class="layer" viewBox="0 0 444 965" aria-hidden="true">
      <path d="M0,210 C120,170 260,160 444,210 L444,160 L0,160 Z" fill="#173f8c"/>
      <path d="M0,210 C120,170 260,160 444,210 L444,235 C300,190 140,190 0,225 Z" fill="#b5121b"/>
      <path d="M0,400 C120,420 240,420 444,360" fill="none" stroke="#1d4fa0" stroke-width="4"/>
      <path d="M0,610 C150,560 280,590 444,640" fill="none" stroke="#1d4fa0" stroke-width="4"/>
      <path d="M0,760 C120,740 200,800 444,770 L444,800 L0,800 Z" fill="#b5121b"/>
      <path d="M0,785 C140,760 230,820 444,790 L444,965 L0,965 Z" fill="#1a3f8a"/>
      <path d="M0,840 C150,815 300,820 444,840 L444,965 L0,965 Z" fill="#163a80"/>
    </svg>

    <h2 class="abs trip-title script">The trip</h2>
    <p class="abs trip-intro">When chartering Tidewren, the vessel is yours to direct anywhere within the time you wish to enjoy her. We do have a few old favorites that are always fun that we have listed below. These are just to provide an idea of the possible cruise as every trip takes into account your ideas and natures (tides, weather and currents) will.Our custom trips are simple to arrange and book, we simply ask for a minimum of 3 hours duration.</p>

    <div class="tour tour--blast">
      <h3 class="tour__title script">2 hour Blast</h3>
      <p class="tour__text">Could be a sunset sail, an early morning wake up cruise or a blast out into the bay anytime to find peace, fresh air and amazing views.</p>
    </div>
    <div class="tour tour--half">
      <h3 class="tour__title script">½ day Fun</h3>
      <p class="tour__text">A full morning, afternoon or evening out in the Bay seeing many of the main features and landmarks close to the Bay from the water. Actual duration 4-5 hours</p>
    </div>
    <div class="tour tour--full">
      <h3 class="tour__title script">Full Day Adventure</h3>
      <p class="tour__text">The day includes a complete circuit of the Bay and lunch at anchor. Actual duration 7-8 hours</p>
    </div>

    <div class="abs badge" role="img" aria-label="Licensed captain credential"></div>
    <h2 class="abs contact-title script">Contact</h2>

    <div class="contact-row contact-row--main condensed">
      <span class="contact-item">
        <svg width="20" height="20" viewBox="0 0 20 20"><circle cx="10" cy="10" r="9" fill="none" stroke="#fff" stroke-width="1.5"/><path d="M7,5.5 L8.6,8 L7.6,9 C8.3,10.6 9.4,11.7 11,12.4 L12,11.4 L14.5,13 L13.4,14.6 C9.5,14.3 5.7,10.5 5.4,6.6 Z" fill="#fff"/></svg>
        +1 (415) 555 SAIL (7245)
      </span>
      <span class="contact-item">
        <svg width="24" height="18" viewBox="0 0 24 18"><rect x="1" y="1" width="22" height="16" fill="none" stroke="#fff" stroke-width="1.5"/><path d="M1,1 L12,10 L23,1 M1,17 L9,8 M23,17 L15,8" fill="none" stroke="#fff" stroke-width="1.5"/></svg>
        Bookings@TidewrenMarine.com
      </span>
    </div>
    <div class="contact-row contact-row--web condensed">
      <span class="contact-item">
        <svg width="17" height="17" viewBox="0 0 20 20"><circle cx="10" cy="10" r="8.5" fill="none" stroke="#fff" stroke-width="1.5"/><ellipse cx="10" cy="10" rx="3.8" ry="8.5" fill="none" stroke="#fff" stroke-width="1.3"/><path d="M1.5,10 H18.5 M3,5.5 H17 M3,14.5 H17" stroke="#fff" stroke-width="1.3"/></svg>
        www.tidewrenmarine.com
      </span>
      <span class="contact-item">
        <svg width="17" height="17" viewBox="0 0 20 20"><circle cx="10" cy="10" r="8.5" fill="none" stroke="#fff" stroke-width="1.5"/></svg>
        /tidewrenmarinellc
      </span>
    </div>
  </section>

</main>
</body>
</html>
```